Group training gym/bootcamp needs a web design

We need a website for our gym that is based in Sydney. We have indoor functional training classes and outdoor bootcamp classes. We would like the web site to have a video (to be created) and photo gallery. I would like the site made on word press and i would like to be able to make minor changes such as changing images and text without having to use a designer.

The website should have the following pages: home page; the gym; the bootcamp; photo gallery; about us; contact.

I have uploaded our logo and i would like to keep to these colour (blue,yellow,silver) and black is also allowed

Target Market(s)

18-50 male and female

Industry/Entity Type

Gym

Coding

Coded - Design and coding required

Number of Pages Required

5+ page

Font styles to use
Sans Serif

Colors
0692cd
fbed22
1b1b1b
e8e8e8

Requirements
Must have
• The website should have the following pages: home page; the gym; the bootcamp; photo gallery; about us; contact.
• I have uploaded our logo and i would like to keep to these colour (blue,yellow,silver) and black is also allowed
• Video upload and photo upload

```html
<!DOCTYPE html>
<html lang="en">
<head>
<meta charset="utf-8">
<title>Kinetic Core Station</title>
<link href="https://fonts.googleapis.com/css2?family=Oswald:wght@400;500;600&family=Open+Sans:wght@400;600;700&display=swap" rel="stylesheet">
<style>
:root{
  --blue:#0692cd;
  --deep-blue:#0b5f8f;
  --navy:#0a4a72;
  --yellow:#fbed22;
  --black:#1b1b1b;
  --silver:#e8e8e8;
  --text:#555;
  --white:#fff;
}
*{margin:0;padding:0;box-sizing:border-box}
html,body{width:1200px;height:2687px;overflow:hidden;background:var(--white)}
body{font-family:"Open Sans",Arial,sans-serif;color:var(--text);position:relative}
.abs{position:absolute}
.heading{font-family:"Oswald",Arial,sans-serif;font-weight:500;text-transform:uppercase;color:var(--black)}

/* hero */
.hero{left:0;top:0;width:1200px;height:555px;background:linear-gradient(120deg,#5d6266 0%,#3c4145 40%,#6f7477 70%,#2f3336 100%)}
.hero-shade{left:0;top:0;width:1200px;height:555px;background:linear-gradient(180deg,rgba(0,0,0,.35),rgba(0,0,0,.1) 40%,rgba(0,0,0,.3))}
.brand{left:98px;top:38px;display:flex;align-items:center;gap:12px}
.brand-dot{width:26px;height:26px;border-radius:50%;background:var(--yellow)}
.brand-name{font-family:"Oswald",Arial,sans-serif;font-weight:600;font-size:26px;color:var(--yellow);text-transform:uppercase;line-height:1}
.topbar{right:98px;top:16px;display:flex;gap:26px;align-items:center;font-size:14px;font-weight:700;color:var(--white)}
.topbar span{display:flex;align-items:center;gap:10px}
.topbar svg{width:26px;height:26px}
.nav{right:98px;top:62px;display:flex;gap:38px;font-family:"Oswald",Arial,sans-serif;font-size:15px;font-weight:500;color:var(--white);text-transform:uppercase;align-items:center}
.nav .active{color:var(--yellow)}
.hero-title{left:0;width:1200px;top:212px;text-align:center;font-family:"Oswald",Arial,sans-serif;font-weight:500;font-size:62px;color:var(--white);text-transform:uppercase;letter-spacing:1px}
.hero-sub{left:0;width:1200px;top:297px;text-align:center;font-size:24px;color:var(--white)}
.btn-ghost{left:510px;top:358px;width:180px;height:46px;border:2px solid var(--white);border-radius:24px;color:var(--white);font-family:"Oswald",Arial,sans-serif;font-size:17px;display:flex;align-items:center;justify-content:center;background:rgba(0,0,0,.15)}
.dots{left:538px;top:494px;display:flex;gap:8px}
.dots i{width:26px;height:4px;background:var(--white);border-radius:2px}
.dots i.on{background:var(--yellow)}

/* welcome */
.welcome-title{left:0;width:1200px;top:620px;text-align:center;font-size:30px}
.welcome-text{left:210px;width:780px;top:688px;text-align:center;font-size:13px;line-height:28px;color:#777}
.wave{left:0;top:1020px}
.service{width:232px;height:232px;border-radius:50%;border:6px solid var(--white);box-shadow:0 0 0 3px #cfd3d6;overflow:hidden}
.service-photo{width:100%;height:100%}
.service-label{position:absolute;left:0;top:112px;width:100%;height:64px;background:rgba(0,0,0,.6);color:var(--white);font-family:"Oswald",Arial,sans-serif;font-size:17px;text-transform:uppercase;text-align:center;line-height:24px;padding-top:8px}

/* what we do */
.doing{left:0;top:1130px;width:1200px;height:470px;background:linear-gradient(90deg,var(--navy),var(--deep-blue) 50%,#0f6ea3)}
.doing-title{left:98px;top:1215px;font-size:27px;color:var(--white)}
.doing-text{left:98px;width:500px;top:1278px;font-size:12px;line-height:25px;color:var(--white)}
.doing-text p+p{margin-top:20px}
.btn-outline{border:2px solid var(--white);border-radius:22px;font-family:"Oswald",Arial,sans-serif;display:flex;align-items:center;justify-content:center}
.read-more{left:98px;top:1482px;width:130px;height:38px;color:var(--yellow);font-size:13px;border-color:#c9d7e0}
.video{left:648px;top:1229px;width:452px;height:290px;border:3px solid var(--white);background:linear-gradient(135deg,#b9b3aa,#8a6b63 45%,#6a7176)}
.play{left:848px;top:1349px}

/* gallery */
.gallery-title{left:0;width:1200px;top:1676px;text-align:center;font-size:30px}
.photo{position:absolute}
.more{left:491px;top:2208px;width:218px;height:44px;border-color:#cfcfcf;color:#d2a90c;font-size:14px}

/* footer */
.footer{left:0;top:2326px;width:1200px;height:361px;background:var(--black);border-top:3px solid var(--yellow)}
.foot-brand{left:98px;top:2480px;display:flex;align-items:center;gap:14px}
.foot-brand .brand-dot{width:34px;height:34px;background:var(--blue)}
.foot-brand .brand-name{font-size:30px}
.foot-head{font-size:17px;color:var(--white);top:2384px}
.foot-list{left:415px;top:2428px;list-style:none;font-size:12px;line-height:23px;color:var(--white)}
.news-text{left:575px;top:2428px;width:250px;font-size:12px;line-height:22px;color:var(--white)}
.news-input{left:575px;top:2482px;width:254px;height:34px;background:var(--white);font-size:11px;color:#999;padding:9px 12px}
.subscribe{left:575px;top:2533px;width:94px;height:32px;color:var(--white);font-size:12px;border-color:#ccc;border-width:1px}
.contact{left:888px;top:2428px;font-size:12px;line-height:20px;color:var(--white)}
.contact-row{display:flex;gap:16px;margin-bottom:16px}
.contact-row svg{width:14px;height:16px;flex:none;margin-top:2px}
.foot-line{left:98px;top:2606px;width:1002px;height:1px;background:#333}
.copy{left:98px;top:2637px;font-size:12px;color:var(--white)}
.social{top:2627px;width:36px;height:36px;border:1px solid #ccc;border-radius:50%}
</style>
</head>
<body>

<!-- hero -->
<div class="abs hero" role="img" aria-label="Group of people doing lunges with medicine balls in an indoor gym"></div>
<div class="abs hero-shade"></div>
<div class="abs brand"><span class="brand-dot"></span><span class="brand-name">Kinetic Core</span></div>
<div class="abs topbar">
  <span><svg viewBox="0 0 26 26"><circle cx="13" cy="13" r="13" fill="#fbed22"/><path d="M9 7l3 3-1.5 2a8 8 0 0 0 4 4l2-1.5 3 3-2 2C12 19 7 14 7 9z" fill="#1b1b1b"/></svg>1 800 555 0199</span>
  <span><svg viewBox="0 0 26 26"><circle cx="13" cy="13" r="13" fill="#fbed22"/><rect x="7" y="9" width="12" height="8" fill="#1b1b1b"/><path d="M7 9l6 5 6-5" stroke="#fbed22" fill="none"/></svg>info@kineticcorestation.com</span>
</div>
<nav class="abs nav">
  <span class="active">Home</span><span>The Gym</span><span>The Bootcamp</span><span>Photo Gallery</span><span>About Us</span><span>Contact Us</span>
  <svg width="16" height="16" viewBox="0 0 16 16"><circle cx="6.5" cy="6.5" r="5" stroke="#fff" stroke-width="2" fill="none"/><path d="M10 10l5 5" stroke="#fff" stroke-width="2"/></svg>
</nav>
<h1 class="abs hero-title">Kinetic Core Station</h1>
<p class="abs hero-sub">We have indoor functional training classes and outdoor bootcamp classes</p>
<div class="abs btn-ghost">BOOK A CLASS</div>
<div class="abs dots"><i class="on"></i><i></i><i></i><i></i></div>

<!-- welcome -->
<h2 class="abs heading welcome-title">Welcome to Kinetic Core Station</h2>
<p class="abs welcome-text">At vero eos et accusamus et iusto odio dignissimos ducimus qui blanditiis praesen iuvol up tatum deleniti atque corrupti quos dolores et qua lestias excepturi sint occaecati cupiditate non provi milique sunt in culp quise offic</p>

<svg class="abs wave" width="1200" height="140" viewBox="0 0 1200 140">
  <path d="M0 5 Q600 170 1200 5 L1200 140 L0 140Z" fill="var(--blue)"/>
  <path d="M0 22 Q600 200 1200 22 L1200 140 L0 140Z" fill="var(--navy)"/>
</svg>
<div class="abs doing"></div>

<div class="abs service" style="left:95px;top:785px"><div class="service-photo" role="img" aria-label="Indoor functional training class" style="background:linear-gradient(160deg,#d9dcde,#7c8185)"></div><div class="service-label">Indoor<br>Functional Training</div></div>
<div class="abs service" style="left:355px;top:838px"><div class="service-photo" role="img" aria-label="Outdoor bootcamp silhouette at sunset" style="background:linear-gradient(180deg,#a9c4d9,#c9b58a 70%,#6e5a3a)"></div><div class="service-label">Outdoor<br>Bootcamp Classes</div></div>
<div class="abs service" style="left:613px;top:838px"><div class="service-photo" role="img" aria-label="Wellness stretching class" style="background:linear-gradient(160deg,#b98e86,#5e5f6e)"></div><div class="service-label">Wellness<br>Program</div></div>
<div class="abs service" style="left:871px;top:785px"><div class="service-photo" role="img" aria-label="Personal trainer with client" style="background:linear-gradient(160deg,#9aa1a6,#3b4045)"></div><div class="service-label">Personal<br>Training</div></div>

<!-- what we do -->
<h2 class="abs heading doing-title">What We Do</h2>
<div class="abs doing-text">
  <p>At vero eos et accusamus et iusto odio dignissimos ducimus qui blanditiis praesen iuvol up tatum deleniti atque corrupti quos dolores et quas.</p>
  <p>Molestias excepturi sint occaecati cupiditate non provident, similique sunt in culp quise officia deserunt mollitia animi, id est laborum et dolorum fuga. Et harum quidem rerum facilis estet expedita distinctio. Nam libero tempore, cum soluta nobis est eligendi optio cumque nihil im pedit quo minus id quod maxime.</p>
</div>
<div class="abs btn-outline read-more">READ MORE &gt;&gt;</div>
<div class="abs video" role="img" aria-label="Video still of people doing sit-ups outdoors"></div>
<svg class="abs play" width="50" height="50" viewBox="0 0 50 50"><circle cx="25" cy="25" r="25" fill="rgba(0,0,0,.75)"/><path d="M20 15l15 10-15 10z" fill="#fff"/></svg>

<!-- gallery -->
<h2 class="abs heading gallery-title">Photo Gallery</h2>
<div class="photo" role="img" aria-label="Outdoor bootcamp group doing lunges on grass" style="left:98px;top:1764px;width:507px;height:393px;background:linear-gradient(180deg,#7fa7c0,#5e7f4a 45%,#4e8a36)"></div>
<div class="photo" role="img" aria-label="Woman training with battle ropes" style="left:616px;top:1764px;width:236px;height:188px;background:linear-gradient(150deg,#4a4e52,#1f2225)"></div>
<div class="photo" role="img" aria-label="Medicine ball workout on the floor" style="left:863px;top:1764px;width:237px;height:188px;background:linear-gradient(150deg,#c7cbcd,#4b5054)"></div>
<div class="photo" role="img" aria-label="Box jumps in the gym" style="left:616px;top:1965px;width:236px;height:192px;background:linear-gradient(150deg,#a8a6a2,#3a3c3f)"></div>
<div class="photo" role="img" aria-label="Group running drill in a brick gym" style="left:863px;top:1965px;width:237px;height:192px;background:linear-gradient(150deg,#9a6a55,#2b2d30)"></div>
<div class="abs btn-outline more">VIEW MORE PHOTOS &gt;&gt;</div>

<!-- footer -->
<footer class="abs footer"></footer>
<div class="abs foot-brand"><span class="brand-dot"></span><span class="brand-name">Kinetic Core</span></div>
<h3 class="abs heading foot-head" style="left:415px">Information</h3>
<ul class="abs foot-list"><li>Home</li><li>The Gym</li><li>The Bootcamp</li><li>Photo Gallery</li><li>About us</li><li>Contact us</li></ul>
<h3 class="abs heading foot-head" style="left:575px">Newsletter Subscription</h3>
<p class="abs news-text">Register your Email Address to get Information about us</p>
<div class="abs news-input">Email Address</div>
<div class="abs btn-outline subscribe">SUBSCRIBE</div>
<h3 class="abs heading foot-head" style="left:888px">Contact Us</h3>
<div class="abs contact">
  <div class="contact-row"><svg viewBox="0 0 14 16"><path d="M7 0a5 5 0 0 1 5 5c0 4-5 11-5 11S2 9 2 5a5 5 0 0 1 5-5z" fill="#fff"/><circle cx="7" cy="5" r="2" fill="#1b1b1b"/></svg><span>Harbour Lane Fitness<br>12 Quarry Street Sydney</span></div>
  <div class="contact-row"><svg viewBox="0 0 14 16"><path d="M2 1l3 3-1.5 2a8 8 0 0 0 4 4l2-1.5 3 3-2 2C5 13 0 8 0 3z" fill="#fff"/></svg><span>1 800 555 0199</span></div>
  <div class="contact-row"><svg viewBox="0 0 14 16"><rect x="0" y="3" width="14" height="10" fill="#fff"/><path d="M0 3l7 5 7-5" stroke="#1b1b1b" fill="none"/></svg><span>info@kineticcorestation.com</span></div>
</div>
<div class="abs foot-line"></div>
<p class="abs copy">Copyrights © 2017, Kinetic Core Station. All rights reserved.</p>
<div class="abs social" style="left:1019px"></div>
<div class="abs social" style="left:1064px"></div>

</body>
</html>
```